OBK Farcoast Logistics Limited

We need the buissnes card to be very exclusive. As we are all young in our company. We need this to be the gate to make our clients feel deep interest for us.

We are focused in as International Trade advisors, and our products go from Oil Tanker Ships to Rubber balls for dogs.

Our Slogan is Bringing Distance Home.
And our main marketing will be through Internet.

We were stablished in 2009 In Mexico and we also have offices in Hong Kong.
We have representatives in China and Europe.

Target Market(s)

Is every company or Individual that wants to develop an International Project or product development or Logistic service of Goods and people.
Some of our current projects are Ship Brokerage, Mine Brokerage, Real State and Product Pormotional development.

Industry/Entity Type

It Company

Requirements
Must have
• Our Logo and slogan, and make the card accoriding to the logo.
Nice to have
• Our Colors

```html
<!DOCTYPE html>
<html lang="en">
<head>
<meta charset="utf-8">
<title>OBK Farcoast Logistics Limited – Business Card</title>
<link rel="stylesheet" href="https://fonts.googleapis.com/css2?family=Source+Sans+3:wght@400;600;700&display=swap">
<style>
  :root {
    --backdrop: #e9e4dc;
    --card: #ffffff;
    --card-edge: #3a3a3a;
    --brand-green: #8cc63f;
    --brand-sky: #29a8e0;
    --brand-navy: #2e3a8c;
    --brand-blue: #2f7fc8;
    --ink: #4a4a4a;
  }
  * { margin: 0; padding: 0; box-sizing: border-box; }
  html, body { width: 1200px; height: 1017px; overflow: hidden; }
  body {
    background: var(--backdrop);
    font-family: "Source Sans 3", "Myriad Pro", sans-serif;
    color: var(--ink);
    position: relative;
  }
  .card {
    position: absolute;
    top: 52px;
    width: 534px;
    height: 935px;
    background: var(--card);
    border: 1px solid var(--card-edge);
    text-align: center;
  }
  .card--front { left: 46px; }
  .card--back { left: 620px; }

  .brand-mark {
    position: absolute;
    left: 50%;
    border-radius: 50%;
    background: radial-gradient(circle at 40% 40%, #e6f4fb 0%, #bfe1f3 100%);
    border: 3px solid var(--brand-blue);
    transform: translateX(-50%);
  }
  .card--front .brand-mark { top: 64px; width: 276px; height: 276px; }
  .card--back .brand-mark { top: 212px; width: 334px; height: 334px; }

  .brand-name {
    position: absolute;
    left: 0; right: 0;
    color: var(--brand-green);
    font-weight: 700;
    line-height: 1;
    letter-spacing: 6px;
  }
  .card--front .brand-name { top: 338px; font-size: 106px; }
  .card--back .brand-name { top: 540px; font-size: 130px; }

  .slogan {
    position: absolute;
    left: 0; right: 0;
    color: var(--brand-sky);
    font-weight: 400;
    line-height: 1;
  }
  .card--front .slogan { top: 437px; font-size: 21px; }
  .card--back .slogan { top: 660px; font-size: 25px; }

  .person-name {
    position: absolute; top: 530px; left: 0; right: 0;
    color: var(--brand-navy);
    font-size: 37px; font-weight: 700; line-height: 1;
  }
  .person-title {
    position: absolute; top: 577px; left: 0; right: 0;
    font-size: 25px; line-height: 1;
  }
  .contact-list {
    position: absolute; top: 644px; left: 0; right: 0;
    list-style: none;
  }
  .contact-list li {
    display: flex; align-items: center; justify-content: center;
    gap: 9px;
    height: 39.5px;
    font-size: 26px;
  }
  .contact-list svg { width: 24px; height: 24px; fill: var(--brand-navy); flex: none; }
  .address {
    position: absolute; top: 830px; left: 0; right: 0;
    font-size: 26px; line-height: 38px;
  }
  .web-line {
    position: absolute; top: 818px; left: 0; right: 0;
    font-size: 30px; letter-spacing: 5.5px; line-height: 1;
  }
</style>
</head>
<body>
  <section class="card card--front">
    <div class="brand-mark"></div>
    <div class="brand-name">OBK</div>
    <div class="slogan">Bringing Distance Home</div>
    <div class="person-name">Your Name</div>
    <div class="person-title">Title</div>
    <ul class="contact-list">
      <li>
        <svg viewBox="0 0 24 24" aria-hidden="true"><circle cx="12" cy="12" r="10.5" fill="none" stroke="#2e3a8c" stroke-width="2"/><path d="M8.5 6.5l2 .3.8 2.6-1.3 1c.6 1.6 1.8 2.9 3.4 3.6l1.1-1.3 2.6.8.3 2-1.6 1.3C11 16.5 7.4 12.8 7.2 8z"/></svg>
        123-456-0789
      </li>
      <li>
        <svg viewBox="0 0 24 24" aria-hidden="true"><rect x="6" y="4" width="12" height="19" rx="2"/><rect x="8.5" y="6.5" width="7" height="5" fill="#fff"/><rect x="14" y="0" width="2" height="5"/><g fill="#fff"><rect x="8.5" y="13.5" width="2" height="2"/><rect x="11" y="13.5" width="2" height="2"/><rect x="13.5" y="13.5" width="2" height="2"/><rect x="8.5" y="17" width="2" height="2"/><rect x="11" y="17" width="2" height="2"/><rect x="13.5" y="17" width="2" height="2"/></g></svg>
        123-456-0789
      </li>
      <li>
        <svg viewBox="0 0 24 24" aria-hidden="true"><path d="M2 9l10-6 10 6v12H2z"/><path d="M5 8h14v6l-7 4-7-4z" fill="#fff"/><path d="M8 10h8v1.3H8zM8 12.5h8v1.3H8z"/></svg>
        info@obkfarcoast.example
      </li>
      <li>
        <svg viewBox="0 0 24 24" aria-hidden="true"><g fill="none" stroke="#2e3a8c" stroke-width="1.6"><circle cx="12" cy="12" r="10"/><ellipse cx="12" cy="12" rx="4.5" ry="10"/><path d="M2 12h20M4 6.5h16M4 17.5h16M12 2v20"/></g></svg>
        www.obkfarcoast.example
      </li>
    </ul>
    <div class="address">Street Name, City Name<br>State Zip Code</div>
  </section>

  <section class="card card--back">
    <div class="brand-mark"></div>
    <div class="brand-name">OBK</div>
    <div class="slogan">Bringing Distance Home</div>
    <div class="web-line">www.obkfarcoast.example</div>
  </section>
</body>
</html>
```